Animal Horse & Bedding Company Needs a Website Coded & Designed

We need a website for a new animal bedding and feed company that is visually grabbing and vibrant. We would like to see a website that displays trust, quality and confidence. Needs to be responsive and mobile friendly for all browsers and coded for both Android & IOS. SEO is also important.

Joomla or Wordpress – must be both desktop and mobile friendly with fast page load speed. Need the ability to edit ourselves in Wordpress or Joomla.

Full details attached below with some layout and content ideas.

Coding

Coded - Design and coding required

Number of Pages Required

5+ page

Font styles to use
Sans Serif

Requirements
Must have
• Needs to be responsive and mobile friendly for all browsers and coded for both Android & IOS. SEO is also important.

Wordpress – must be both desktop and mobile friendly with fast page load speed. Need the ability to edit ourselves in Wordpress.

Logo Colours:
Dark Brown
CMYK: 50 / 70 / 80 / 70
Pantone: 4625C

Orange
CMYK: 0 / 50 / 100 / 0
Pantone: 144C
Nice to have
• Use picture of building attached and super impose logo on building.

```html
<!DOCTYPE html>
<html lang="en">
<head>
<meta charset="utf-8">
<title>Haybarrow Bedding &amp; Feed</title>
<link rel="stylesheet" href="https://fonts.googleapis.com/css2?family=Oswald:wght@400;500;600&family=Open+Sans:wght@400;600;700&display=swap">
<style>
:root{
  --brown:#3b2314;
  --orange:#f7941d;
  --cream:#fdf0e2;
  --text:#4a3a30;
  --white:#ffffff;
}
*{box-sizing:border-box;margin:0;padding:0}
html,body{width:1200px;height:3105px;overflow:hidden}
body{position:relative;background:var(--white);font-family:"Open Sans",sans-serif;color:var(--text)}
.abs{position:absolute}
.head{font-family:"Oswald",sans-serif;text-transform:uppercase;color:var(--brown)}
.topbar{left:0;top:0;width:1200px;height:25px;background:var(--brown);color:#fff;font-size:11px;font-weight:700}
.topbar .call{left:193px;top:5px}
.topbar .call b{color:var(--orange)}
.topbar .follow{left:970px;top:4px;display:flex;align-items:center;gap:3px;font-size:10px}
.dot{display:inline-block;border-radius:50%;background:var(--orange)}
.topbar .dot{width:12px;height:12px}
.hero{left:0;top:25px;width:1200px;height:646px;background:linear-gradient(180deg,#cfe3f3 0%,#e6eef5 40%,#9fb08a 55%,#7d8f5e 65%,#a4302e 72%,#b9b2a6 82%,#6f8450 100%)}
.nav{top:60px;font-family:"Oswald",sans-serif;font-size:19px;font-weight:500;color:var(--brown);text-transform:uppercase}
.brand{font-family:"Oswald",sans-serif;font-weight:400;color:var(--brown);text-transform:uppercase;letter-spacing:2px;display:flex;align-items:center;gap:10px}
.brand .dot{width:44px;height:44px}
.nav-brand{left:452px;top:44px;font-size:36px}
.btn{display:flex;align-items:center;justify-content:center;border-radius:16px;font-family:"Oswald",sans-serif;text-transform:uppercase;font-size:15px}
.btn.fill{background:var(--brown);color:var(--orange)}
.btn.line{border:2px solid var(--orange);color:var(--brown);background:rgba(255,255,255,.35)}
.hero-title{left:0;top:146px;width:1200px;text-align:center;font-size:41px;line-height:41px;font-weight:600}
.welcome-brand{left:117px;top:760px}
.welcome-brand small{display:block;font-family:"Oswald",sans-serif;font-size:15px;color:var(--brown)}
.welcome-brand span{font-size:40px}
.copy{font-size:11.6px;line-height:16px}
.feature{width:150px;text-align:center}
.feature .dot{width:34px;height:34px;border:2px solid var(--brown);margin:0 auto 12px}
.feature h3{font-size:13px;font-weight:700;color:var(--brown);text-transform:uppercase;line-height:16px}
.feature p{font-size:9.5px;line-height:12px;margin-top:12px}
.photo{border:1px solid var(--brown)}
.section-title{display:flex;align-items:center;gap:12px;font-size:40px}
.section-title .dot{width:46px;height:46px}
.body-copy{font-size:15px;line-height:16px;text-align:justify}
.ticks{list-style:none;font-size:15px}
.ticks li{display:flex;align-items:center;gap:18px;height:24px}
.ticks svg{flex:none}
.more{display:flex;align-items:center;gap:12px;height:26px;border-radius:13px;background:var(--brown);color:var(--orange);font-size:10px;font-weight:700;letter-spacing:1px;padding:0 18px 0 8px}
.more .dot{width:16px;height:16px}
.news-bg{left:0;top:2624px;width:1200px;height:202px;background:linear-gradient(180deg,#e9eef2 0%,#d7dee3 55%,#a9a37a 80%,#7f7a4a 100%)}
.news-title{left:343px;top:2672px;font-size:34px;letter-spacing:1px;font-weight:600}
.news-input{left:316px;top:2730px;width:710px;height:50px;background:#fff;border:1px solid #c9c0b6;font-size:14px;padding:17px 0 0 38px;color:#333}
.news-btn{left:1024px;top:2730px;width:127px;height:50px;background:var(--brown);color:#fff;font-weight:700;font-size:15px;display:flex;align-items:center;justify-content:center}
.footer{left:0;top:2826px;width:1200px;height:235px;background:var(--brown)}
.footer-brand{left:130px;top:2870px;width:240px;text-align:center;color:#fff;font-family:"Oswald",sans-serif;text-transform:uppercase;font-size:36px;letter-spacing:2px}
.footer-brand .dot{width:52px;height:52px;display:block;margin:0 auto 16px}
.fcol h4{font-family:"Oswald",sans-serif;font-weight:400;font-size:15px;color:var(--orange);text-decoration:underline;margin-bottom:12px}
.fcol li{list-style:none;color:#fff;font-size:11px;line-height:18.5px;display:flex;align-items:center;gap:10px}
.fcol li i{display:inline-block;width:0;height:0;border-left:6px solid var(--orange);border-top:4px solid transparent;border-bottom:4px solid transparent}
.fcol li b{display:inline-block;width:8px;height:8px;border-radius:50%;background:var(--orange)}
.f-email{left:910px;top:2911px;width:163px;height:27px;background:#fff;font-size:9px;padding:8px 0 0 14px;color:#777}
.f-send{left:1046px;top:2911px;width:26px;height:27px;background:var(--orange);display:flex;align-items:center;justify-content:center}
.f-social{left:913px;top:2981px;display:flex;gap:3px}
.f-social .dot{width:17px;height:17px;background:#fff}
.bottombar{left:0;top:3061px;width:1200px;height:44px;background:var(--orange);color:var(--brown);font-size:12px}
</style>
</head>
<body>

<div class="abs topbar">
  <div class="abs call">Call Us : <b>+1 555 010 2244</b></div>
  <div class="abs follow">Follow Us: <span class="dot"></span><span class="dot"></span><span class="dot"></span><span class="dot"></span><span class="dot"></span></div>
</div>

<div class="abs hero" role="img" aria-label="Aerial photo of red barns, paddocks and fields under a cloudy sky"></div>
<div class="abs nav" style="left:135px;top:60px">Home</div>
<div class="abs nav" style="left:232px;top:60px">About</div>
<div class="abs nav" style="left:335px;top:60px">Feed</div>
<div class="abs brand nav-brand"><span class="dot"></span>Haybarrow</div>
<div class="abs nav" style="left:800px;top:52px;font-size:17px">Bedding</div>
<div class="abs nav" style="left:902px;top:52px;font-size:17px">Contact Us</div>
<div class="abs btn fill" style="left:1002px;top:49px;width:128px;height:32px">Request Quote</div>
<div class="abs head hero-title">The Best Bedding &amp; Feed for<br>your horse livestock or household pet</div>
<div class="abs btn fill" style="left:492px;top:264px;width:111px;height:32px">Contact Us</div>
<div class="abs btn line" style="left:630px;top:264px;width:111px;height:32px">Request Quote</div>

<div class="abs brand welcome-brand"><span class="dot" style="width:56px;height:56px"></span><div><small>Welcome to</small><span>Haybarrow</span></div></div>
<div class="abs copy" style="left:117px;top:855px;width:463px">
  <p>Looking for the best bedding and feed for your horse, livestock or household pet look no further. We use premium locally sourced straw and hay in all of our products and are committed in providing quality products and service.</p><br>
  <p>Your animal deserves the very best in health and comfort to keep them healthy, strong and happy. Our products are designed for horses, livestock (goats, cattle and sheep), small caged animals (rabbits, guinea pigs and more).</p><br>
  <p>Haybarrow offers supply and delivery of fresh bedding as well as removal of waste bedding. Let us deliver you a container of fresh straw and haul your waste bedding away. A full service solution that is sustainable and responsible.</p>
</div>
<div class="abs feature" style="left:95px;top:1055px"><span class="dot" style="display:block"></span><h3>Quality<br>Guaranteed</h3><p>Grown for quality -<br>100% natural with no<br>chemicals or additives</p></div>
<div class="abs feature" style="left:267px;top:1055px"><span class="dot" style="display:block"></span><h3>Full Service<br>Solution</h3><p>Dedicated in providing<br>a full service solution of bedding<br>supply &amp; waste removal</p></div>
<div class="abs feature" style="left:434px;top:1055px"><span class="dot" style="display:block"></span><h3>Convenient &amp;<br>Cost Effective</h3><p>Compressed bags, pellets or<br>bulk products saving<br>in shipping costs</p></div>
<div class="abs" style="left:650px;top:771px;width:400px;height:428px;border-radius:48% 48% 50% 50%;background:radial-gradient(circle at 55% 55%,#8a5a2e 0%,#c98b3a 45%,#f7941d 70%,#fbe3c3 100%)" role="img" aria-label="Horse standing in tall grass framed by a large horseshoe"></div>

<div class="abs" style="left:0;top:1313px;width:1200px;height:659px;background:var(--cream)"></div>
<div class="abs photo" style="left:113px;top:1423px;width:516px;height:434px;background:linear-gradient(160deg,#7a4a22 0%,#2a1a0e 30%,#d8a94a 60%,#e9c36a 100%)" role="img" aria-label="Mare and foal resting on a bed of golden straw"></div>
<div class="abs head section-title" style="left:692px;top:1440px"><span class="dot"></span>Bedding</div>
<p class="abs body-copy" style="left:696px;top:1524px;width:388px">Hay cubes and pellets are made from premium hay offering a variety of animals a feed that is non-GMO and packed with natural nutrients. These pellets and cubes are less bulky to handle, store and ship.As well, they reduce the amount of wasted feed.</p>
<ul class="abs ticks" style="left:700px;top:1622px">
  <li><svg width="12" height="12" viewBox="0 0 12 12"><circle cx="6" cy="6" r="6" fill="#3b2314"/><path d="M3 6.2l2 2 4-4.2" stroke="#fff" stroke-width="1.6" fill="none"/></svg>100% Natural Chopped Straw</li>
  <li><svg width="12" height="12" viewBox="0 0 12 12"><circle cx="6" cy="6" r="6" fill="#3b2314"/><path d="M3 6.2l2 2 4-4.2" stroke="#fff" stroke-width="1.6" fill="none"/></svg>Low Dust</li>
  <li><svg width="12" height="12" viewBox="0 0 12 12"><circle cx="6" cy="6" r="6" fill="#3b2314"/><path d="M3 6.2l2 2 4-4.2" stroke="#fff" stroke-width="1.6" fill="none"/></svg>Chemical &amp; Additive Free</li>
  <li><svg width="12" height="12" viewBox="0 0 12 12"><circle cx="6" cy="6" r="6" fill="#3b2314"/><path d="M3 6.2l2 2 4-4.2" stroke="#fff" stroke-width="1.6" fill="none"/></svg>Clean &amp; Highly Absorbent</li>
  <li><svg width="12" height="12" viewBox="0 0 12 12"><circle cx="6" cy="6" r="6" fill="#3b2314"/><path d="M3 6.2l2 2 4-4.2" stroke="#fff" stroke-width="1.6" fill="none"/></svg>Cheaper than Wood Shavings</li>
  <li><svg width="12" height="12" viewBox="0 0 12 12"><circle cx="6" cy="6" r="6" fill="#3b2314"/><path d="M3 6.2l2 2 4-4.2" stroke="#fff" stroke-width="1.6" fill="none"/></svg>Economic – less used &amp; less wasted</li>
  <li><svg width="12" height="12" viewBox="0 0 12 12"><circle cx="6" cy="6" r="6" fill="#3b2314"/><path d="M3 6.2l2 2 4-4.2" stroke="#fff" stroke-width="1.6" fill="none"/></svg>Environmentally Friendly – Recyclable &amp; Compostable</li>
</ul>
<div class="abs more" style="left:699px;top:1823px"><span class="dot"></span>READ MORE</div>

<div class="abs head section-title" style="left:110px;top:2078px"><span class="dot"></span>Feeding</div>
<p class="abs body-copy" style="left:116px;top:2163px;width:386px">Hay cubes and pellets are made from premium hay offering a variety of animals a feed that is non-GMO and packed with natural nutrients. These pellets and cubes are less bulky to handle, store and ship.As well, they reduce the amount of wasted feed.</p>
<ul class="abs ticks" style="left:112px;top:2262px">
  <li style="gap:8px"><svg width="12" height="12" viewBox="0 0 12 12"><circle cx="6" cy="6" r="6" fill="#3b2314"/><path d="M3 6.2l2 2 4-4.2" stroke="#fff" stroke-width="1.6" fill="none"/></svg>100% Natural</li>
  <li style="gap:8px"><svg width="12" height="12" viewBox="0 0 12 12"><circle cx="6" cy="6" r="6" fill="#3b2314"/><path d="M3 6.2l2 2 4-4.2" stroke="#fff" stroke-width="1.6" fill="none"/></svg>Chemical &amp; Additive Free</li>
  <li style="gap:8px"><svg width="12" height="12" viewBox="0 0 12 12"><circle cx="6" cy="6" r="6" fill="#3b2314"/><path d="M3 6.2l2 2 4-4.2" stroke="#fff" stroke-width="1.6" fill="none"/></svg>Available in Pellets or Cubes</li>
  <li style="gap:8px"><svg width="12" height="12" viewBox="0 0 12 12"><circle cx="6" cy="6" r="6" fill="#3b2314"/><path d="M3 6.2l2 2 4-4.2" stroke="#fff" stroke-width="1.6" fill="none"/></svg>High Protein Content</li>
  <li style="gap:8px"><svg width="12" height="12" viewBox="0 0 12 12"><circle cx="6" cy="6" r="6" fill="#3b2314"/><path d="M3 6.2l2 2 4-4.2" stroke="#fff" stroke-width="1.6" fill="none"/></svg>Eliminate Waste In Feeding</li>
  <li style="gap:8px"><svg width="12" height="12" viewBox="0 0 12 12"><circle cx="6" cy="6" r="6" fill="#3b2314"/><path d="M3 6.2l2 2 4-4.2" stroke="#fff" stroke-width="1.6" fill="none"/></svg>Clean - Eliminates Dust From Feeding Baled Hay</li>
  <li style="gap:8px"><svg width="12" height="12" viewBox="0 0 12 12"><circle cx="6" cy="6" r="6" fill="#3b2314"/><path d="M3 6.2l2 2 4-4.2" stroke="#fff" stroke-width="1.6" fill="none"/></svg>Cost Effective</li>
</ul>
<div class="abs more" style="left:112px;top:2467px"><span class="dot"></span>READ MORE</div>
<div class="abs photo" style="left:608px;top:2058px;width:513px;height:469px;background:linear-gradient(135deg,#8a5a2a 0%,#c9c2b8 35%,#b8a06a 60%,#2b2118 100%)" role="img" aria-label="Close-up of a horse muzzle eating hay"></div>

<div class="abs news-bg" role="img" aria-label="Mare and foal in a grassy field under a cloudy sky"></div>
<div class="abs head news-title">Subscribe to Newsletter</div>
<div class="abs news-input">Enter Your Email</div>
<div class="abs news-btn">SUBSCRIBE</div>

<div class="abs footer"></div>
<div class="abs footer-brand"><span class="dot"></span>Haybarrow</div>
<div class="abs fcol" style="left:451px;top:2874px"><h4>QUICK LINKS</h4><ul><li><i></i>Home</li><li><i></i>About</li><li><i></i>Feed</li><li><i></i>Bedding</li><li><i></i>Contact Us</li></ul></div>
<div class="abs fcol" style="left:653px;top:2876px"><h4>CONTACT US</h4><ul><li><b></b>1200 Meadow Road</li><li style="padding-left:18px">Fairbanks, Alaska 99701</li><li><b></b>555-210-4471</li><li><b></b>info@haybarrowfeed.com</li><li><b></b>haybarrowfeed.com</li></ul></div>
<div class="abs fcol" style="left:913px;top:2874px"><h4>NEWSLETTER</h4></div>
<div class="abs f-email">Email Address</div>
<div class="abs f-send"><svg width="10" height="10" viewBox="0 0 10 10"><path d="M2 1l7 4-7 4z" fill="#3b2314"/></svg></div>
<div class="abs fcol" style="left:913px;top:2945px"><h4>FOLLOW US</h4></div>
<div class="abs f-social"><span class="dot"></span><span class="dot"></span><span class="dot"></span><span class="dot"></span><span class="dot"></span></div>

<div class="abs bottombar">
  <span class="abs" style="left:127px;top:14px">Copyright © 2021, Northgate Studio, All Right Reserved</span>
  <span class="abs" style="left:928px;top:14px">Delivery in Canada &amp; USA</span>
</div>

</body>
</html>
```